Business Card for Professional Photographer

I'm looking for an eye catching modern clean design that compliments my logo/ website fonts & colours.
I specialise in architecture, corporate & commercial photography so I'm marketing to professional clients rather than portrait / wedding clients.

I would prefer to not have a solid black design.

My logo brand guide is as follows :

Main front font. : Reislust
Main font colour : #fff
Slogan front font : Ubuntu Bold
Monogram front font : Venti Medium
Container colour : #fff

I need print ready files in pdf .png & .eps formats.

Included in the files below are some screen grabs as reference to font & colours etc.

```html
<!DOCTYPE html>
<html lang="en">
<head>
<meta charset="utf-8">
<title>Clearframe Studio – Business Card</title>
<link href="https://fonts.googleapis.com/css2?family=Ubuntu:wght@400;500;700&family=Open+Sans:wght@400;600&display=swap" rel="stylesheet">
<style>
  :root {
    --backdrop: #d9d9d9;
    --gold-light: #fbeeb8;
    --gold-mid: #e4bd78;
    --gold-deep: #cf9d5c;
    --gold-text: #c7924f;
    --slate: #555555;
    --slate-text: #6c6c6c;
    --ink: #4a4a4a;
    --paper: #ffffff;
  }
  * { box-sizing: border-box; margin: 0; padding: 0; }
  html, body { width: 1200px; height: 874px; overflow: hidden; }
  body {
    background: var(--backdrop);
    display: flex;
    flex-direction: column;
    align-items: center;
    justify-content: center;
    gap: 30px;
  }
  .card {
    width: 680px;
    height: 388px;
    border-radius: 24px;
    position: relative;
    overflow: hidden;
    box-shadow: 0 6px 18px rgba(0,0,0,0.18);
  }

  /* Front */
  .card-front {
    background: radial-gradient(ellipse at 48% 50%, var(--gold-light) 0%, var(--gold-mid) 55%, var(--gold-deep) 100%);
  }
  .front-brand {
    position: absolute;
    left: 96px;
    top: 118px;
    font-family: "Ubuntu", sans-serif;
    color: var(--slate-text);
  }
  .front-name {
    font-size: 27px;
    font-weight: 400;
    letter-spacing: 5px;
  }
  .front-tagline {
    font-size: 10px;
    font-weight: 700;
    letter-spacing: 2.4px;
    margin-top: 4px;
  }
  .front-web {
    font-size: 15px;
    letter-spacing: 4.5px;
    margin-top: 8px;
  }
  .front-circle {
    position: absolute;
    right: 82px;
    top: 104px;
    width: 170px;
    height: 170px;
    border-radius: 50%;
    border: 12px solid #8a8a8a;
    opacity: 0.9;
  }

  /* Back */
  .card-back { background: var(--paper); }
  .back-identity {
    position: absolute;
    right: 386px;
    top: 112px;
    text-align: right;
    font-family: "Ubuntu", sans-serif;
  }
  .person-name {
    font-size: 26px;
    font-weight: 500;
    color: var(--gold-text);
  }
  .person-title {
    font-size: 16px;
    font-weight: 500;
    color: var(--ink);
    margin-top: 2px;
  }
  .divider {
    position: absolute;
    left: 318px;
    top: 104px;
    width: 2px;
    height: 140px;
    background: #9a9a9a;
  }
  .contact-list {
    position: absolute;
    left: 338px;
    top: 104px;
    list-style: none;
    font-family: "Open Sans", sans-serif;
    font-size: 16px;
    color: var(--ink);
    line-height: 21px;
  }
  .contact-list li { display: flex; align-items: center; gap: 8px; }
  .contact-list svg { width: 13px; height: 13px; fill: var(--gold-text); flex: none; }
  .contact-list .address { padding-left: 0; }
  .footer-band {
    position: absolute;
    left: 0;
    right: 0;
    bottom: 48px;
    height: 74px;
    background: var(--slate);
    display: flex;
    align-items: center;
    justify-content: space-between;
    padding: 0 60px 0 48px;
  }
  .footer-web {
    font-family: "Ubuntu", sans-serif;
    font-size: 19px;
    letter-spacing: 4px;
    color: var(--paper);
  }
  .footer-mark {
    width: 34px;
    height: 34px;
    border-radius: 50%;
    border: 3px solid var(--gold-text);
  }
</style>
</head>
<body>
  <section class="card card-front">
    <div class="front-brand">
      <div class="front-name">CLEARFRAME STUDIO</div>
      <div class="front-tagline">Architecture Corporate Commercial</div>
      <div class="front-web">www.clearframestudio.com</div>
    </div>
    <div class="front-circle" aria-hidden="true"></div>
  </section>

  <section class="card card-back">
    <div class="back-identity">
      <div class="person-name">Daniel Reyes</div>
      <div class="person-title">President</div>
    </div>
    <div class="divider"></div>
    <ul class="contact-list">
      <li><svg viewBox="0 0 16 16"><path d="M3 1l3 3-1.5 2a9 9 0 0 0 5.5 5.5L12 10l3 3-2 2C7 15 1 9 1 3z"/></svg>555-210-4418</li>
      <li><svg viewBox="0 0 16 16"><path d="M4 0h8a1 1 0 0 1 1 1v14a1 1 0 0 1-1 1H4a1 1 0 0 1-1-1V1a1 1 0 0 1 1-1zm1 2v10h6V2zm3 11a1 1 0 1 0 0 2 1 1 0 0 0 0-2z"/></svg>555-318-6027</li>
      <li><svg viewBox="0 0 16 16"><path d="M4 1h8v4H4zM1 6h14v7h-3v2H4v-2H1zm4 5v3h6v-3z"/></svg>555-472-9135</li>
      <li><svg viewBox="0 0 16 16"><path d="M1 3h14v10H1zm1.5 1.5L8 9l5.5-4.5z"/></svg>hello@clearframestudio.com</li>
      <li class="address">1420 Alder Court</li>
      <li class="address">Juneau, Alaska 99801</li>
    </ul>
    <div class="footer-band">
      <span class="footer-web">www.clearframestudio.com</span>
      <span class="footer-mark" aria-hidden="true"></span>
    </div>
  </section>
</body>
</html>
```